Association qui souhaite améliorer l'accès aux personnes en situation de handicap

Nous sommes une association qui a pour objectif d'améliorer l'accessibilité, augmenter l'offre des activités réalisables dans notre région touristique.
Nous souhaitons réaliser un site internet afin de pouvoir communiquer sur notre association. Nous avons déjà conçu notre flyer sur Plumotrix. Nous souhaiterions une base graphique se rapportant à celui-ci. C'est possible de tout retravailler mais nous souhaitons tout de même retrouver la charte graphique ou code couleur du flyer.
Il nous faudrait quelques pages:
- 1 page : Acceuil / Présentation (Home), Il y aurait le descriptif de l'association, avec ses objectifs à +/- moyen terme
- 1 page : Nos réalisations, celle-ci présenterait les éléments que nous avons réalisés avec des zones de textes et des images classées chronologiquement au fur et à mesure des nouveautés
- 1 page : Media, comme la précédente, mais ou on pourrait voir ou lire sur les divers médias qui parlent de nous
- 1 page : Evenements : c'est une page pour présenter divers activités que nous allons organiser
- 1 page : Contact qui indique comment nous contacter et avec la présentation des 5 ou 6 membres du comité
- 1 link donate : qui arrive sur un formulaire de donnée que l'on pourra faire évoluer sur un système de payement par la suite. Cette bannière doit se retrouver sur toutes les pages
Il est nécessaire que se design puisse être transféré sur une lecture sur téléphone mobile
Personnes en situation de handicap
Associatif

```html
<!DOCTYPE html>
<html lang="en">
<head>
<meta charset="utf-8">
<title>Reachwide Association – Website Design Board</title>
<link href="https://fonts.googleapis.com/css2?family=Raleway:wght@400;500;600&family=Oswald:wght@400;500&family=Mulish:wght@400;600;700&display=swap" rel="stylesheet">
<style>
:root{
  --red:#c8102e;
  --ink:#1b1b1b;
  --text:#444;
  --muted:#777;
  --dark:#262626;
  --black:#050505;
  --paper:#ffffff;
  --cream:#fbfaf5;
  --line:#bdbdbd;
  --board:#ffffff;
}
*{margin:0;padding:0;box-sizing:border-box}
html,body{width:1200px;height:1200px;overflow:hidden;background:var(--board)}
body{position:relative;font-family:'Mulish',sans-serif;color:var(--ink)}
.abs{position:absolute}

.board-label{position:absolute;font-family:'Raleway',sans-serif;font-weight:400;font-size:23px;letter-spacing:5px;color:var(--ink);white-space:nowrap;transform:translate(-50%,-50%) rotate(-90deg)}

/* ---------- desktop page ---------- */
.page{position:absolute;top:30px;width:413px;height:1147px;background:var(--paper);overflow:hidden;box-shadow:0 2px 10px rgba(0,0,0,.12)}
.topbar{position:absolute;left:0;top:0;width:100%;height:9px;background:var(--red);color:#fff;font-size:3px}
.topbar .dots{position:absolute;left:45px;top:3px;display:flex;gap:4px}
.topbar .dots i{display:block;width:3px;height:3px;border-radius:50%;background:#fff}
.topbar .phone{position:absolute;right:45px;top:3px}
.brand{position:absolute;display:flex;align-items:center;gap:2px;font-family:'Mulish',sans-serif;font-weight:700;color:var(--ink);white-space:nowrap}
.brand i{display:block;background:var(--red)}
.nav{position:absolute;left:186px;top:17px;display:flex;gap:14px;font-size:3.2px;color:var(--ink)}
.nav .active{color:var(--red);border-bottom:.5px solid var(--red)}
.donate{position:absolute;background:var(--red);color:#fff;border-radius:10px;font-weight:700;text-align:center}
.btn{position:absolute;background:var(--red);color:#fff;border-radius:8px;font-weight:700;display:flex;align-items:center;gap:3px;white-space:nowrap}
.btn::before{content:"";display:block;border:.5px solid #fff;border-radius:50%}
.d-btn{height:12px;padding:0 6px 0 2px;font-size:3px}
.d-btn::before{width:8px;height:8px}
.kicker{position:absolute;font-family:'Oswald',sans-serif;font-weight:500;color:var(--ink);white-space:nowrap}
.title{position:absolute;font-family:'Raleway',sans-serif;font-weight:500;white-space:nowrap}
.title b{color:var(--red);font-weight:600}
.para{position:absolute;color:var(--text);line-height:1.55}
.photo{position:absolute}
.ph-warm{background:linear-gradient(135deg,#e9b9c2,#b7737e 55%,#8a4a50)}
.ph-green{background:linear-gradient(135deg,#6f8e3d,#a7b870 45%,#46602a)}
.ph-lake{background:linear-gradient(120deg,#2b3a34,#5d6f66 45%,#9fa9a2 70%,#3d463f)}
.ph-field{background:linear-gradient(135deg,#3f3a36,#8a7a62 40%,#6f8f4a 75%,#2f3a25)}
.ph-snow{background:linear-gradient(135deg,#d9dde3,#9aa6b5 50%,#4c4c55)}
.ph-room{background:linear-gradient(135deg,#c9b89a,#8c7a5d 50%,#e4dccb)}
.ph-kid{background:linear-gradient(180deg,#6c9f46,#4a7d2e 60%,#3f3a86)}
.ph-group{background:linear-gradient(135deg,#5a5d63,#9aa09a 50%,#3b3e48)}
.ph-rust{background:linear-gradient(135deg,#6b4a3a,#a45a4a 50%,#c98f7a)}
.dark-sec{position:absolute;left:0;width:100%;background:var(--dark);color:#fff}
.center{text-align:center;left:0;width:100%}
.media-card{position:absolute;top:577px;width:103px;height:71px}
.caption{position:absolute;left:9px;right:9px;bottom:-5px;height:12px;background:#fff;box-shadow:0 1px 3px rgba(0,0,0,.15);font-size:3.3px;display:flex;align-items:center;justify-content:center;color:var(--ink)}
.caption b{color:var(--red);margin-left:2px}
.event-card{position:absolute;top:721px;width:103px;height:127px;background:#fff;color:var(--ink)}
.event-card .photo{left:0;top:0;width:100%;height:71px}
.date{position:absolute;left:5px;top:5px;width:10px;height:11px;background:var(--red);color:#fff;font-size:2.4px;text-align:center;line-height:1.3;padding-top:2px}
.event-card h4{position:absolute;left:8px;top:78px;font-family:'Raleway',sans-serif;font-weight:600;font-size:5px}
.event-card p{position:absolute;left:8px;top:88px;width:88px;font-size:3.3px;color:var(--muted);line-height:1.5}
.event-card .btn{left:8px;top:107px}
.field{position:absolute;height:12px;border:.5px solid var(--line);background:#fff;font-size:3px;color:var(--muted);padding:3px 3px}
.submit{position:absolute;background:var(--red);color:#fff;font-size:3px;display:flex;align-items:center;justify-content:center}
.foot-head{position:absolute;font-family:'Oswald',sans-serif;font-size:4.2px;color:var(--red)}
.foot-list{position:absolute;font-size:3.2px;color:#fff;line-height:2.45}
.social{position:absolute;display:flex;gap:5px}
.social i{display:block;width:6px;height:6px;border-radius:50%;background:var(--red)}
.contact-row{position:absolute;display:flex;align-items:center;gap:3px;font-size:3.2px;color:#fff;white-space:nowrap}
.contact-row svg{flex:none}
.copy{position:absolute;font-size:3px;color:#fff;text-align:center;left:0;width:100%}
.copy b{color:var(--red);font-weight:400}

/* ---------- mobile page ---------- */
.mobile{position:absolute;left:995px;top:55px;width:95px;height:1120px;background:var(--paper);overflow:hidden;box-shadow:0 2px 10px rgba(0,0,0,.12)}
.m-btn{height:9px;padding:0 4px 0 1.5px;font-size:2.4px;left:50%;transform:translateX(-50%)}
.m-btn::before{width:6px;height:6px}
.m-para{position:absolute;left:5px;width:85px;font-size:3.1px;line-height:1.6;color:var(--text);text-align:center}
.m-title{position:absolute;left:0;width:100%;text-align:center;font-family:'Raleway',sans-serif;font-weight:500;white-space:nowrap}
.m-title b{color:var(--red);font-weight:600}
</style>
</head>
<body>

<div class="board-label" style="left:39px;top:628px">DESKTOP VERSION</div>
<div class="board-label" style="left:1147px;top:878px">MOBILE VIEW</div>

<!-- ================= Desktop page A : light hero ================= -->
<section class="page" style="left:80px">
  <div class="topbar"><div class="dots"><i></i><i></i><i></i></div><div class="phone">+2 (555) 240 7300</div></div>
  <div class="brand" style="left:45px;top:15px;font-size:4.2px"><i style="width:5px;height:5px"></i>REACHWIDE ASSOCIATION</div>
  <nav class="nav"><span class="active">Home</span><span>Our Achievements</span><span>Media</span><span>Events</span><span>Contacts</span></nav>
  <div class="donate" style="left:336px;top:16px;width:32px;height:10px;font-size:3.3px;line-height:10px">DONATE</div>

  <div class="kicker" style="left:45px;top:72px;font-size:7px">ACCESS THE</div>
  <div class="title" style="left:45px;top:84px;font-size:15px;font-weight:600">TOURIST <b>REGION</b></div>
  <p class="para" style="left:45px;top:108px;width:150px;font-size:3.6px">The resources of the association come from subscriptions, donations and events organized throughout the year.</p>
  <div class="btn d-btn" style="left:45px;top:127px">READ MORE</div>
  <div class="photo ph-warm" role="img" aria-label="Smiling women with a wheelchair user under a greenhouse, cropped in a triangle" style="left:203px;top:36px;width:190px;height:148px;clip-path:polygon(0 5%,100% 75%,0 100%)"></div>

  <div class="photo ph-green" role="img" aria-label="Visually impaired man with a white cane walking on a forest boardwalk" style="left:45px;top:206px;width:158px;height:126px"></div>
  <div class="kicker" style="left:210px;top:219px;font-size:5px">WELCOME TO</div>
  <div class="title" style="left:210px;top:230px;font-size:12px">Reachwide <b>Association</b></div>
  <p class="para" style="left:210px;top:251px;width:158px;font-size:3.6px">Sed ut perspiciatis unde omnis iste natus error sit voluptatem accusantium doloremque laudantium, totam rem aperiam, eaque ipsa quae ab illo inventore veritatis et quasi architecto beatae vitae dicta sunt explicabo. Nemo enim ipsam voluptatem quia voluptas sit aspernatur aut odit aut fugit, sed quia consequuntur magni dolores eos qui ratione voluptatem sequi nesciunt.</p>
  <div class="btn d-btn" style="left:210px;top:300px">READ MORE</div>

  <div class="dark-sec" style="top:355px;height:177px"></div>
  <div class="photo ph-field" role="img" aria-label="Hand touching tall grass beside a wheelchair wheel" style="left:206px;top:355px;width:207px;height:177px;clip-path:polygon(22% 0,100% 0,100% 100%,78% 100%,0 51%)"></div>
  <div class="title" style="left:45px;top:400px;font-size:11px;color:#fff">Our Achievements</div>
  <p class="para" style="left:45px;top:420px;width:158px;font-size:3.6px;color:#ddd">Sed ut perspiciatis unde omnis iste natus error sit voluptatem accusantium doloremque laudantium, totam rem aperiam, eaque ipsa quae ab illo inventore veritatis et quasi architecto beatae vitae dicta sunt explicabo. Nemo enim ipsam voluptatem quia voluptas sit aspernatur aut odit aut fugit, sed quia consequuntur magni dolores eos qui ratione voluptatem sequi nesciunt.</p>
  <div class="btn d-btn" style="left:45px;top:473px">READ MORE</div>

  <div class="title center" style="top:552px;font-size:11px">Our Media</div>
  <div class="para center" style="top:569px;font-size:3.6px">Sed ut perspiciatis unde omnis iste natus error sit voluptatem</div>
  <div class="media-card" style="left:45px"><div class="photo ph-green" role="img" aria-label="Volunteer greeting an elderly man outdoors" style="inset:0"></div><div class="caption">Voluptas Sit Aspernatur<b>+</b></div></div>
  <div class="media-card" style="left:155px"><div class="photo ph-snow" role="img" aria-label="Volunteers helping a person in the snow" style="inset:0"></div><div class="caption">Voluptas Sit Aspernatur<b>+</b></div></div>
  <div class="media-card" style="left:265px"><div class="photo ph-room" role="img" aria-label="Caregiver with an elderly man indoors" style="inset:0"></div><div class="caption">Voluptas Sit Aspernatur<b>+</b></div></div>

  <div class="dark-sec" style="top:677px;height:195px;background:linear-gradient(180deg,#2b2b2b,#3a3a3a 50%,#1e1e1e)"></div>
  <div class="title center" style="top:699px;font-size:11px;color:#fff">Recent Event</div>
  <div class="event-card" style="left:45px"><div class="photo ph-kid" role="img" aria-label="Child blowing a dandelion on a lawn"></div><div class="date">12<br>MAY</div><h4>Neque Porro Wuisquam</h4><p>Sed ut perspiciatis unde omnis iste natus error sit voluptatem accusantium</p><div class="btn d-btn">READ MORE</div></div>
  <div class="event-card" style="left:155px"><div class="photo ph-group" role="img" aria-label="Group gathering on a terrace with wheelchair users"></div><div class="date">12<br>MAY</div><h4>Neque Porro Wuisquam</h4><p>Sed ut perspiciatis unde omnis iste natus error sit voluptatem accusantium</p><div class="btn d-btn">READ MORE</div></div>
  <div class="event-card" style="left:265px"><div class="photo ph-group" role="img" aria-label="Wheelchair athletes at an outdoor event"></div><div class="date">12<br>MAY</div><h4>Neque Porro Wuisquam</h4><p>Sed ut perspiciatis unde omnis iste natus error sit voluptatem accusantium</p><div class="btn d-btn">READ MORE</div></div>

  <div class="abs" style="left:0;top:872px;width:100%;height:160px;background:var(--cream)"></div>
  <div class="photo ph-rust" role="img" aria-label="Smiling person photo cropped in a triangle" style="left:45px;top:895px;width:138px;height:109px;clip-path:polygon(0 0,100% 75%,0 100%)"></div>
  <div class="title" style="left:209px;top:910px;font-size:11px">Contact Us</div>
  <div class="para" style="left:209px;top:926px;font-size:3.6px">Sed ut perspiciatis unde omnis iste natus error</div>
  <div class="field" style="left:209px;top:943px;width:79px">Name:</div>
  <div class="field" style="left:209px;top:959px;width:79px">Email:</div>
  <div class="field" style="left:209px;top:975px;width:79px">Phone:</div>
  <div class="field" style="left:290px;top:943px;width:78px;height:29px">Comments:</div>
  <div class="submit" style="left:290px;top:975px;width:78px;height:12px">SUBMIT</div>

  <svg class="abs" style="left:0;top:989px" width="413" height="158" viewBox="0 0 413 158"><polygon points="0,18 162,38 413,0 413,158 0,158" fill="#050505"/></svg>
  <div class="brand" style="left:45px;top:1050px;font-size:4.5px;color:#fff"><i style="width:6px;height:6px"></i>REACHWIDE ASSOCIATION</div>
  <p class="para" style="left:45px;top:1070px;width:72px;font-size:3.2px;color:#ddd">Sed ut perspiciatis unde omnis iste natus error sit voluptatem accusantium rem aperiam</p>
  <div class="social" style="left:45px;top:1093px"><i></i><i></i><i></i></div>
  <div class="foot-head" style="left:155px;top:1046px">SITEMAP</div>
  <div class="foot-list" style="left:155px;top:1054px">Home<br>Our Achivements<br>Media<br>Events<br>Contact Us</div>
  <div class="foot-head" style="left:231px;top:1046px">OTHERS</div>
  <div class="foot-list" style="left:231px;top:1054px">Privacy Policy<br>Terms &amp; Conditions<br>Leagal<br>Donate<br>Help / Support</div>
  <div class="foot-head" style="left:301px;top:1046px">CONTACTS</div>
  <div class="contact-row" style="left:301px;top:1055px"><svg width="7" height="7" viewBox="0 0 10 10"><circle cx="5" cy="5" r="4.5" fill="none" stroke="#c8102e"/><path d="M5 2.5a1.6 1.6 0 0 1 1.6 1.6C6.6 5.5 5 7.5 5 7.5S3.4 5.5 3.4 4.1A1.6 1.6 0 0 1 5 2.5z" fill="#c8102e"/></svg>Corvan Road 42 Val Serein</div>
  <div class="contact-row" style="left:301px;top:1070px"><svg width="7" height="7" viewBox="0 0 10 10"><circle cx="5" cy="5" r="4.5" fill="none" stroke="#c8102e"/><path d="M3.3 2.8l1 1-.5.7a3.5 3.5 0 0 0 1.7 1.7l.7-.5 1 1-.7.8C4.8 7.3 2.7 5.2 2.5 3.5z" fill="#c8102e"/></svg>+2 (555) 240 7300</div>
  <div class="contact-row" style="left:301px;top:1085px"><svg width="7" height="7" viewBox="0 0 10 10"><circle cx="5" cy="5" r="4.5" fill="none" stroke="#c8102e"/><rect x="2.8" y="3.5" width="4.4" height="3" fill="none" stroke="#c8102e" stroke-width=".7"/><path d="M2.8 3.5L5 5.2 7.2 3.5" fill="none" stroke="#c8102e" stroke-width=".7"/></svg>info@reachwideassociation.org</div>
  <div class="copy" style="top:1124px">Copyright © 2022 <b>Reachwide Association</b>. All Rights Reserved.</div>
</section>

<!-- ================= Desktop page B : photo hero ================= -->
<section class="page" style="left:519px">
  <div class="topbar"><div class="dots"><i></i><i></i><i></i></div><div class="phone">+2 (555) 240 7300</div></div>
  <div class="brand" style="left:45px;top:15px;font-size:4.2px"><i style="width:5px;height:5px"></i>REACHWIDE ASSOCIATION</div>
  <nav class="nav"><span class="active">Home</span><span>Our Achievements</span><span>Media</span><span>Events</span><span>Contacts</span></nav>
  <div class="donate" style="left:336px;top:16px;width:32px;height:10px;font-size:3.3px;line-height:10px">DONATE</div>

  <div class="photo ph-lake" role="img" aria-label="Woman in a wheelchair by a misty forest lake" style="left:0;top:31px;width:413px;height:153px"></div>
  <div class="kicker" style="left:45px;top:72px;font-size:7px;color:#fff">ACCESS THE</div>
  <div class="title" style="left:45px;top:84px;font-size:15px;font-weight:600;color:#fff">TOURIST <b>REGION</b></div>
  <p class="para" style="left:45px;top:108px;width:150px;font-size:3.6px;color:#eee">The resources of the association come from subscriptions, donations and events organized throughout the year.</p>
  <div class="btn d-btn" style="left:45px;top:127px">READ MORE</div>
  <div class="abs" style="left:45px;top:171px;display:flex;gap:4px"><i style="width:4px;height:4px;border-radius:50%;background:var(--red)"></i><i style="width:4px;height:4px;border-radius:50%;background:#fff"></i><i style="width:4px;height:4px;border-radius:50%;background:#fff"></i></div>

  <div class="photo ph-green" role="img" aria-label="Visually impaired man with a white cane walking on a forest boardwalk, cropped in a triangle" style="left:45px;top:206px;width:158px;height:126px;clip-path:polygon(0 0,100% 80%,0 100%)"></div>
  <div class="kicker" style="left:210px;top:219px;font-size:5px">WELCOME TO</div>
  <div class="title" style="left:210px;top:230px;font-size:12px">Reachwide <b>Association</b></div>
  <p class="para" style="left:210px;top:251px;width:158px;font-size:3.6px">Sed ut perspiciatis unde omnis iste natus error sit voluptatem accusantium doloremque laudantium, totam rem aperiam, eaque ipsa quae ab illo inventore veritatis et quasi architecto beatae vitae dicta sunt explicabo. Nemo enim ipsam voluptatem quia voluptas sit aspernatur aut odit aut fugit, sed quia consequuntur magni dolores eos qui ratione voluptatem sequi nesciunt.</p>
  <div class="btn d-btn" style="left:210px;top:300px">READ MORE</div>

  <div class="dark-sec" style="top:355px;height:177px"></div>
  <div class="photo ph-field" role="img" aria-label="Hand touching tall grass beside a wheelchair wheel" style="left:206px;top:355px;width:207px;height:177px;clip-path:polygon(22% 0,100% 0,100% 100%,78% 100%,0 51%)"></div>
  <div class="title" style="left:45px;top:400px;font-size:11px;color:#fff">Our Achievements</div>
  <p class="para" style="left:45px;top:420px;width:158px;font-size:3.6px;color:#ddd">Sed ut perspiciatis unde omnis iste natus error sit voluptatem accusantium doloremque laudantium, totam rem aperiam, eaque ipsa quae ab illo inventore veritatis et quasi architecto beatae vitae dicta sunt explicabo. Nemo enim ipsam voluptatem quia voluptas sit aspernatur aut odit aut fugit, sed quia consequuntur magni dolores eos qui ratione voluptatem sequi nesciunt.</p>
  <div class="btn d-btn" style="left:45px;top:473px">READ MORE</div>

  <div class="title center" style="top:552px;font-size:11px">Our Media</div>
  <div class="para center" style="top:569px;font-size:3.6px">Sed ut perspiciatis unde omnis iste natus error sit voluptatem</div>
  <div class="media-card" style="left:45px"><div class="photo ph-green" role="img" aria-label="Volunteer greeting an elderly man outdoors" style="inset:0"></div><div class="caption">Voluptas Sit Aspernatur<b>+</b></div></div>
  <div class="media-card" style="left:155px"><div class="photo ph-snow" role="img" aria-label="Volunteers helping a person in the snow" style="inset:0"></div><div class="caption">Voluptas Sit Aspernatur<b>+</b></div></div>
  <div class="media-card" style="left:265px"><div class="photo ph-room" role="img" aria-label="Caregiver with an elderly man indoors" style="inset:0"></div><div class="caption">Voluptas Sit Aspernatur<b>+</b></div></div>

  <div class="dark-sec" style="top:677px;height:195px;background:linear-gradient(180deg,#2b2b2b,#3a3a3a 50%,#1e1e1e)"></div>
  <div class="title center" style="top:699px;font-size:11px;color:#fff">Recent Event</div>
  <div class="event-card" style="left:45px"><div class="photo ph-kid" role="img" aria-label="Child blowing a dandelion on a lawn"></div><div class="date">12<br>MAY</div><h4>Neque Porro Wuisquam</h4><p>Sed ut perspiciatis unde omnis iste natus error sit voluptatem accusantium</p><div class="btn d-btn">READ MORE</div></div>
  <div class="event-card" style="left:155px"><div class="photo ph-group" role="img" aria-label="Group gathering on a terrace with wheelchair users"></div><div class="date">12<br>MAY</div><h4>Neque Porro Wuisquam</h4><p>Sed ut perspiciatis unde omnis iste natus error sit voluptatem accusantium</p><div class="btn d-btn">READ MORE</div></div>
  <div class="event-card" style="left:265px"><div class="photo ph-group" role="img" aria-label="Wheelchair athletes at an outdoor event"></div><div class="date">12<br>MAY</div><h4>Neque Porro Wuisquam</h4><p>Sed ut perspiciatis unde omnis iste natus error sit voluptatem accusantium</p><div class="btn d-btn">READ MORE</div></div>

  <div class="abs" style="left:0;top:872px;width:100%;height:160px;background:var(--cream)"></div>
  <div class="photo ph-rust" role="img" aria-label="Smiling person photo cropped in a triangle" style="left:45px;top:895px;width:138px;height:109px;clip-path:polygon(0 0,100% 75%,0 100%)"></div>
  <div class="title" style="left:209px;top:910px;font-size:11px">Contact Us</div>
  <div class="para" style="left:209px;top:926px;font-size:3.6px">Sed ut perspiciatis unde omnis iste natus error</div>
  <div class="field" style="left:209px;top:943px;width:79px">Name:</div>
  <div class="field" style="left:209px;top:959px;width:79px">Email:</div>
  <div class="field" style="left:209px;top:975px;width:79px">Phone:</div>
  <div class="field" style="left:290px;top:943px;width:78px;height:29px">Comments:</div>
  <div class="submit" style="left:290px;top:975px;width:78px;height:12px">SUBMIT</div>

  <svg class="abs" style="left:0;top:989px" width="413" height="158" viewBox="0 0 413 158"><polygon points="0,18 162,38 413,0 413,158 0,158" fill="#050505"/></svg>
  <div class="brand" style="left:45px;top:1050px;font-size:4.5px;color:#fff"><i style="width:6px;height:6px"></i>REACHWIDE ASSOCIATION</div>
  <p class="para" style="left:45px;top:1070px;width:72px;font-size:3.2px;color:#ddd">Sed ut perspiciatis unde omnis iste natus error sit voluptatem accusantium rem aperiam</p>
  <div class="social" style="left:45px;top:1093px"><i></i><i></i><i></i></div>
  <div class="foot-head" style="left:155px;top:1046px">SITEMAP</div>
  <div class="foot-list" style="left:155px;top:1054px">Home<br>Our Achivements<br>Media<br>Events<br>Contact Us</div>
  <div class="foot-head" style="left:231px;top:1046px">OTHERS</div>
  <div class="foot-list" style="left:231px;top:1054px">Privacy Policy<br>Terms &amp; Conditions<br>Leagal<br>Donate<br>Help / Support</div>
  <div class="foot-head" style="left:301px;top:1046px">CONTACTS</div>
  <div class="contact-row" style="left:301px;top:1055px"><svg width="7" height="7" viewBox="0 0 10 10"><circle cx="5" cy="5" r="4.5" fill="none" stroke="#c8102e"/><path d="M5 2.5a1.6 1.6 0 0 1 1.6 1.6C6.6 5.5 5 7.5 5 7.5S3.4 5.5 3.4 4.1A1.6 1.6 0 0 1 5 2.5z" fill="#c8102e"/></svg>Corvan Road 42 Val Serein</div>
  <div class="contact-row" style="left:301px;top:1070px"><svg width="7" height="7" viewBox="0 0 10 10"><circle cx="5" cy="5" r="4.5" fill="none" stroke="#c8102e"/><path d="M3.3 2.8l1 1-.5.7a3.5 3.5 0 0 0 1.7 1.7l.7-.5 1 1-.7.8C4.8 7.3 2.7 5.2 2.5 3.5z" fill="#c8102e"/></svg>+2 (555) 240 7300</div>
  <div class="contact-row" style="left:301px;top:1085px"><svg width="7" height="7" viewBox="0 0 10 10"><circle cx="5" cy="5" r="4.5" fill="none" stroke="#c8102e"/><rect x="2.8" y="3.5" width="4.4" height="3" fill="none" stroke="#c8102e" stroke-width=".7"/><path d="M2.8 3.5L5 5.2 7.2 3.5" fill="none" stroke="#c8102e" stroke-width=".7"/></svg>info@reachwideassociation.org</div>
  <div class="copy" style="top:1124px">Copyright © 2022 <b>Reachwide Association</b>. All Rights Reserved.</div>
</section>

<!-- ================= Mobile page ================= -->
<section class="mobile">
  <div class="brand" style="left:27px;top:5px;font-size:3.3px"><i style="width:4px;height:4px"></i>REACHWIDE ASSOCIATION</div>
  <div class="abs" style="left:0;top:17px;width:95px;height:15px;background:var(--black)"></div>
  <svg class="abs" style="left:5px;top:21px" width="9" height="7" viewBox="0 0 9 7"><path d="M0 .5h9M0 3.5h9M0 6.5h9" stroke="#fff" stroke-width=".8"/></svg>
  <div class="donate" style="left:64px;top:21px;width:26px;height:7px;font-size:2.6px;line-height:7px">DONATE</div>

  <div class="photo ph-warm" role="img" aria-label="Smiling women with a wheelchair user, cropped in a triangle" style="left:5px;top:34px;width:85px;height:64px;clip-path:polygon(0 0,100% 80%,0 100%)"></div>
  <div class="kicker" style="left:0;width:95px;text-align:center;top:97px;font-size:5.5px">ACCESS THE</div>
  <div class="m-title" style="top:104px;font-size:7.5px;font-weight:600">TOURIST <b>REGION</b></div>
  <p class="m-para" style="top:115px">The resources of the association come from subscriptions, donations and events organized throughout the year.</p>
  <div class="btn m-btn" style="top:139px">READ MORE</div>

  <div class="photo ph-green" role="img" aria-label="Visually impaired man with a white cane walking on a forest boardwalk" style="left:5px;top:160px;width:85px;height:68px"></div>
  <div class="kicker" style="left:0;width:95px;text-align:center;top:234px;font-size:3.8px">WELCOME TO</div>
  <div class="m-title" style="top:240px;font-size:7px">Reachwide <b>Association</b></div>
  <p class="m-para" style="top:251px">Sed ut perspiciatis unde omnis iste natus error sit voluptatem accusantium doloremque laudantium, totam rem aperiam, eaque ipsa quae ab illo inventore veritatis et quasi architecto beatae vitae dicta sunt explicabo.</p>
  <div class="btn m-btn" style="top:293px">READ MORE</div>

  <div class="abs" style="left:0;top:318px;width:95px;height:160px;background:var(--dark)"></div>
  <div class="photo ph-field" role="img" aria-label="Hand touching tall grass beside a wheelchair wheel" style="left:0;top:318px;width:95px;height:77px;clip-path:polygon(10% 0,100% 0,100% 100%,0 60%)"></div>
  <div class="m-title" style="top:404px;font-size:7px;color:#fff">Our Achievements</div>
  <p class="m-para" style="top:415px;color:#ddd">Sed ut perspiciatis unde omnis iste natus error sit voluptatem accusantium doloremque laudantium, totam rem aperiam, eaque ipsa quae ab illo inventore veritatis et quasi architecto beatae vitae dicta sunt explicabo.</p>
  <div class="btn m-btn" style="top:461px">READ MORE</div>

  <div class="m-title" style="top:484px;font-size:6.5px">Our Media</div>
  <p class="m-para" style="top:493px">Sed ut perspiciatis unde omnis iste natus</p>
  <div class="abs" style="left:3px;top:521px;font-size:5px;color:var(--ink)">‹</div>
  <div class="abs" style="right:3px;top:521px;font-size:5px;color:var(--ink)">›</div>
  <div class="photo ph-green" role="img" aria-label="Volunteer greeting an elderly man outdoors" style="left:10px;top:500px;width:74px;height:45px"></div>
  <div class="caption" style="left:15px;right:auto;width:64px;top:543px;bottom:auto;height:7px;font-size:2.4px;position:absolute">Voluptas Sit Aspernatur<b>+</b></div>

  <div class="abs" style="left:0;top:559px;width:95px;height:120px;background:linear-gradient(180deg,#2b2b2b,#1e1e1e)"></div>
  <div class="m-title" style="top:564px;font-size:6.5px;color:#fff">Recent Event</div>
  <div class="abs" style="left:3px;top:616px;font-size:5px;color:#fff">‹</div>
  <div class="abs" style="right:3px;top:616px;font-size:5px;color:#fff">›</div>
  <div class="abs" style="left:10px;top:578px;width:74px;height:94px;background:#fff">
    <div class="photo ph-kid" role="img" aria-label="Child blowing a dandelion on a lawn" style="left:0;top:0;width:74px;height:50px"></div>
    <div class="date" style="left:4px;top:4px;width:8px;height:9px;font-size:2px;padding-top:1.5px">12<br>MAY</div>
    <div class="abs" style="left:5px;top:54px;font-family:'Raleway',sans-serif;font-weight:600;font-size:3.8px">Neque Porro Wuisquam</div>
    <p class="abs" style="left:5px;top:61px;width:64px;font-size:2.7px;color:var(--muted);line-height:1.5">Sed ut perspiciatis unde omnis iste natus error sit voluptatem...</p>
    <div class="btn m-btn" style="left:5px;transform:none;top:74px;height:7px;font-size:2.1px"><span>READ MORE</span></div>
  </div>

  <div class="photo ph-rust" role="img" aria-label="Smiling person photo cropped in a triangle" style="left:5px;top:682px;width:85px;height:68px;clip-path:polygon(0 0,100% 80%,0 100%)"></div>
  <div class="m-title" style="top:751px;font-size:7px">Contact Us</div>
  <p class="m-para" style="top:761px">Sed ut perspiciatis unde omnis iste natus</p>
  <div class="field" style="left:5px;top:770px;width:85px;height:12px;font-size:2.8px">Name:</div>
  <div class="field" style="left:5px;top:786px;width:85px;height:12px;font-size:2.8px">Email:</div>
  <div class="field" style="left:5px;top:802px;width:85px;height:12px;font-size:2.8px">Phone:</div>
  <div class="field" style="left:5px;top:818px;width:85px;height:27px;font-size:2.8px">Comments:</div>
  <div class="submit" style="left:5px;top:848px;width:85px;height:12px;font-size:3px">SUBMIT</div>

  <svg class="abs" style="left:0;top:862px" width="95" height="258" viewBox="0 0 95 258"><polygon points="0,12 95,0 95,258 0,258" fill="#050505"/></svg>
  <div class="brand" style="left:5px;top:883px;font-size:3.6px;color:#fff"><i style="width:5px;height:5px"></i>REACHWIDE ASSOCIATION</div>
  <p class="abs" style="left:5px;top:893px;width:82px;font-size:3px;line-height:1.6;color:#ddd">Sed ut perspiciatis unde omnis iste natus error sit voluptatem accusantium rem aperiam</p>
  <div class="social" style="left:5px;top:917px"><i></i><i></i><i></i></div>
  <div class="foot-head" style="left:5px;top:931px;font-size:4px">SITEMAP</div>
  <div class="foot-list" style="left:5px;top:940px;font-size:3px;line-height:3.3">Home<br>Our Achivements<br>Media<br>Events<br>Contact Us</div>
  <div class="foot-head" style="left:51px;top:931px;font-size:4px">OTHERS</div>
  <div class="foot-list" style="left:51px;top:940px;font-size:3px;line-height:3.3">Privacy Policy<br>Terms &amp; Conditions<br>Leagal<br>Donate<br>Help / Support</div>
  <div class="foot-head" style="left:5px;top:1000px;font-size:4px">CONTACTS</div>
  <div class="contact-row" style="left:5px;top:1011px;font-size:3px"><svg width="8" height="8" viewBox="0 0 10 10"><circle cx="5" cy="5" r="4.5" fill="none" stroke="#c8102e"/><path d="M5 2.5a1.6 1.6 0 0 1 1.6 1.6C6.6 5.5 5 7.5 5 7.5S3.4 5.5 3.4 4.1A1.6 1.6 0 0 1 5 2.5z" fill="#c8102e"/></svg>Corvan Road 42 Val Serein</div>
  <div class="contact-row" style="left:5px;top:1028px;font-size:3px"><svg width="8" height="8" viewBox="0 0 10 10"><circle cx="5" cy="5" r="4.5" fill="none" stroke="#c8102e"/><path d="M3.3 2.8l1 1-.5.7a3.5 3.5 0 0 0 1.7 1.7l.7-.5 1 1-.7.8C4.8 7.3 2.7 5.2 2.5 3.5z" fill="#c8102e"/></svg>+2 (555) 240 7300</div>
  <div class="contact-row" style="left:5px;top:1045px;font-size:3px"><svg width="8" height="8" viewBox="0 0 10 10"><circle cx="5" cy="5" r="4.5" fill="none" stroke="#c8102e"/><rect x="2.8" y="3.5" width="4.4" height="3" fill="none" stroke="#c8102e" stroke-width=".7"/><path d="M2.8 3.5L5 5.2 7.2 3.5" fill="none" stroke="#c8102e" stroke-width=".7"/></svg>info@reachwideassociation.org</div>
  <div class="copy" style="top:1070px;font-size:3px;line-height:1.6">Copyright © 2022 <b>Reachwide Association</b>.<br>All Rights Reserved.</div>
</section>

</body>
</html>
```